Lendquay wedsite and logo refresh

We are looking for someone to refresh the look and feel of Lendquay.co.nz we are moving it towards a more traditional brokerage.

Target Market(s)

30 to 55 year old professionals

Coding

Coded - Design and coding required

Number of Pages Required

3 page

Requirements
Nice to have
• we are needing a modern professional look

```html
<!DOCTYPE html>
<html lang="en">
<head>
<meta charset="utf-8">
<title>Lendquay – Find and Compare Rates</title>
<link href="https://fonts.googleapis.com/css2?family=Montserrat:wght@500;600;700;800&family=Roboto:wght@400;500&display=swap" rel="stylesheet">
<style>
:root{
  --brand:#ea4620;
  --brand-soft:#f3a58c;
  --brand-pale:#f8d0c1;
  --ink:#1e1e1e;
  --text:#4a4a4a;
  --muted:#6b6b6b;
  --page:#efefef;
  --card:#ffffff;
  --line:#dddddd;
  --footer:#1b1b1b;
}
*{box-sizing:border-box;margin:0;padding:0}
html,body{width:1200px;height:3866px;overflow:hidden}
body{position:relative;background:var(--page);font-family:Roboto,Arial,sans-serif;color:var(--text)}
.abs{position:absolute}
.head{font-family:Montserrat,Arial,sans-serif}

/* header */
.topbar{left:0;top:0;width:1200px;height:63px;background:var(--brand)}
.brand{left:172px;top:17px;font-family:Montserrat,sans-serif;font-weight:600;font-size:24px;color:#fff;letter-spacing:1px}
.nav a{position:absolute;top:24px;font-family:Montserrat,sans-serif;font-weight:700;font-size:13px;color:#fff;text-decoration:none;letter-spacing:.3px}
.btn-login{left:682px;top:15px;width:93px;height:33px;border:2px solid #fff;border-radius:17px;color:#fff;font:700 11px Montserrat,sans-serif;display:flex;align-items:center;justify-content:center}
.btn-signup{left:791px;top:15px;width:123px;height:33px;background:#fff;border-radius:17px;color:var(--brand);font:700 11px Montserrat,sans-serif;display:flex;align-items:center;justify-content:center}
.burger{left:928px;top:24px;width:26px}
.burger i{display:block;height:2px;background:#fff;margin-bottom:5px}
.flag{top:22px;width:32px;height:20px}

/* hero */
.hero-ring{left:622px;top:-8px;width:640px;height:620px;border-radius:50%;background:var(--brand-pale)}
.hero-ring2{left:652px;top:-18px;width:600px;height:590px;border-radius:50%;background:var(--brand-soft)}
.hero-photo{left:680px;top:-40px;width:560px;height:600px;border-radius:50%;background:linear-gradient(135deg,#cfc6bd,#8e8179 55%,#e7e2dc)}
.hero-title{left:172px;top:198px;font:700 34px/40px Montserrat,sans-serif;color:var(--ink);letter-spacing:.5px}
.hero-text{left:172px;top:288px;width:420px;font-size:16px;line-height:24px;color:#333}
.btn-primary{background:var(--brand);color:#fff;border-radius:26px;font:700 14px Montserrat,sans-serif;display:flex;align-items:center;justify-content:center;letter-spacing:.3px}
.hero-btn{left:172px;top:383px;width:248px;height:52px}

/* compare strip */
.compare{left:172px;top:692px;width:856px;height:181px;background:var(--card);box-shadow:0 4px 14px rgba(0,0,0,.08)}
.compare h3{position:absolute;left:46px;top:60px;font:700 23px/30px Montserrat,sans-serif;color:var(--ink)}
.compare p{position:absolute;left:323px;top:60px;width:300px;font-size:13px;line-height:22px;color:#555}
.compare .btn-primary{position:absolute;left:699px;top:72px;width:104px;height:36px;font-size:12px}

.section-title{left:0;width:1200px;text-align:center;font:700 30px Montserrat,sans-serif;color:var(--ink);letter-spacing:.5px}

/* rate cards */
.card{width:202px;height:210px;background:var(--card);box-shadow:0 2px 8px rgba(0,0,0,.08);text-align:center}
.card svg{position:absolute;left:73px;top:30px;width:56px;height:56px}
.card h4{position:absolute;left:0;top:110px;width:100%;font:700 16px/20px Montserrat,sans-serif;color:var(--ink)}
.card p{position:absolute;left:14px;width:174px;font-size:13px;line-height:16px;color:var(--muted)}
.ico{fill:none;stroke:var(--brand);stroke-width:2.6;stroke-linecap:round;stroke-linejoin:round}
.ico .f{fill:var(--brand);stroke:none}

/* about */
.about{left:0;top:1767px;width:1200px;height:579px;background:var(--brand)}
.about h2{position:absolute;left:172px;top:125px;font:800 46px Montserrat,sans-serif;color:#fff;letter-spacing:1px}
.about .lead{position:absolute;left:172px;top:185px;width:400px;font:600 21px/22px Montserrat,sans-serif;color:#fde5dc}
.about .body{position:absolute;left:172px;top:293px;width:390px;font-size:13px;line-height:19px;color:#fff}
.btn-ghost{position:absolute;left:174px;top:408px;width:132px;height:35px;border:2px solid #fff;border-radius:18px;color:#fff;font:700 12px Montserrat,sans-serif;display:flex;align-items:center;justify-content:center}
.about .blob-back{position:absolute;left:640px;top:95px;width:440px;height:440px;border-radius:46% 54% 48% 52%/55% 45% 55% 45%;background:#ef6a44}
.about .blob{position:absolute;left:600px;top:85px;width:470px;height:425px;border-radius:52% 48% 40% 60%/46% 52% 48% 54%;background:linear-gradient(140deg,#e9d8c8,#a89180 50%,#5f6770)}

/* why */
.why-sub{left:0;width:1200px;text-align:center;top:2455px;font-size:16px;color:#555}
.why{width:200px;text-align:center}
.why .ring{position:absolute;left:47px;top:0;width:106px;height:106px;border:2.5px solid var(--brand);border-radius:50%}
.why .dot{position:absolute;left:35px;top:40px;width:25px;height:25px;border-radius:50%;background:#8a8a8a}
.why svg{position:absolute;left:73px;top:25px;width:56px;height:56px}
.why h5{position:absolute;left:0;top:128px;width:100%;font:700 15px/19px Roboto,sans-serif;color:var(--ink)}
.why p{position:absolute;left:5px;top:170px;width:190px;font-size:13px;line-height:16px;color:#555}

/* blog */
.blog-bg{left:0;top:2862px;width:1200px;height:666px;background:#fff}
.blog-feature{left:172px;top:2990px;width:472px;height:407px;background:linear-gradient(135deg,#d8d2cb,#8b7a6e 45%,#cfd6dc)}
.blog-feature-card{left:217px;top:3255px;width:379px;height:165px;background:#fff;box-shadow:0 3px 12px rgba(0,0,0,.1);padding:28px 28px}
.date{color:var(--brand);font-size:16px;display:flex;align-items:center;gap:5px}
.blog-feature-card h4{font:400 19px Roboto,sans-serif;color:var(--ink);margin:6px 0 8px}
.blog-feature-card p{font-size:12px;line-height:18px;color:#444}
.post{left:672px;width:357px;height:124px;border:1px solid var(--line);background:#fff}
.post .thumb{position:absolute;left:10px;top:10px;width:121px;height:103px}
.post .txt{position:absolute;left:144px;top:28px;width:200px}
.post .date{font-size:12px}
.post h6{font:400 17px Roboto,sans-serif;color:var(--ink);margin:4px 0 6px}
.post p{font-size:11px;line-height:15px;color:#666}

/* footer */
.footer{left:0;top:3528px;width:1200px;height:338px;background:var(--footer)}
.email{position:absolute;left:290px;top:65px;width:478px;height:48px;background:#fff;border-radius:24px;padding-left:24px;display:flex;align-items:center;font-size:13px;color:#444}
.footer .btn-primary{position:absolute;left:777px;top:65px;width:133px;height:48px;font-size:13px}
.rule{position:absolute;left:290px;top:152px;width:676px;height:1px;background:#3a3a3a}
.fnav{position:absolute;top:176px;font:500 14px Roboto,sans-serif;color:#fff}
.copy{position:absolute;left:0;top:228px;width:1200px;text-align:center;font-size:12px;color:#ddd}
.social{position:absolute;top:266px;width:14px;height:14px;border-radius:50%;background:#fff}
</style>
</head>
<body>

<!-- header -->
<div class="abs topbar"></div>
<div class="abs brand">LENDQUAY</div>
<nav class="nav">
  <a style="left:414px">SERVICES</a>
  <a style="left:508px">ABOUT</a>
  <a style="left:586px">CONTACT</a>
</nav>
<div class="abs btn-login">LOGIN</div>
<div class="abs btn-signup">SIGN UP FREE</div>
<div class="abs burger"><i></i><i></i><i></i></div>
<div class="abs flag" style="left:977px;background:#233a8f"></div>
<div class="abs flag" style="left:1017px;background:#e0231c"></div>

<!-- hero -->
<div class="abs hero-ring"></div>
<div class="abs hero-ring2"></div>
<div class="abs hero-photo" role="img" aria-label="Photo of a smiling family of three sitting together at home"></div>
<h1 class="abs hero-title">NO OBLIGATIONS<br>NO FEES NO WORRIES</h1>
<p class="abs hero-text">Lorem ipsum dolor sit amet, consectetur adipiscing elit, sed do eiusmod tempor incididunt ut labore et dolore magna aliquaenim ad minim.</p>
<div class="abs btn-primary hero-btn">FIND COMPARE RATES</div>

<!-- compare strip -->
<div class="abs compare">
  <h3>Lendquay<br>Compare Rates</h3>
  <p>Lorem ipsum dolor sit amet, consectetur adipisc ing elit, sed do eiusmod tempor incididunt ut lab ore et dolore magna aliquaenim ad minim.</p>
  <div class="btn-primary">COMPARE</div>
</div>

<h2 class="abs section-title" style="top:938px">FIND AND COMPARE RATES</h2>

<!-- row 1 -->
<div class="abs card" style="left:172px;top:1012px">
  <svg class="ico" viewBox="0 0 56 56"><path d="M6 28 28 8l22 20M12 23v25h32V23M23 48V34h10v14"/></svg>
  <h4>Mortage Rates</h4><p style="top:145px">Lorem ipsum dolor sit am econsectetur adiiscn</p>
</div>
<div class="abs card" style="left:390px;top:1012px">
  <svg class="ico" viewBox="0 0 56 56"><path d="M8 30c0-8 8-13 18-13h6c8 0 14 5 14 12l5 2v7l-5 1-4 6v5h-6v-4h-10v4h-6v-6c-6-2-12-6-12-14z"/><circle cx="40" cy="12" r="9"/><path d="M40 7v10M37 10h5a2 2 0 0 1 0 4h-4"/></svg>
  <h4>Personal Finance</h4><p style="top:145px">Lorem ipsum dolor sit am econsectetur adiiscn</p>
</div>
<div class="abs card" style="left:607px;top:1012px">
  <svg class="ico" viewBox="0 0 56 56"><path d="M8 38V28l6-12h28l6 12v10zM10 38v6h6v-6M40 38v6h6v-6M12 27h32"/><circle class="f" cx="16" cy="32" r="2.5"/><circle class="f" cx="40" cy="32" r="2.5"/></svg>
  <h4>Vehicle Finance</h4><p style="top:145px">Lorem ipsum dolor sit am econsectetur adiiscn</p>
</div>
<div class="abs card" style="left:825px;top:1012px">
  <svg class="ico" viewBox="0 0 56 56"><rect class="f" x="8" y="32" width="7" height="16"/><rect class="f" x="19" y="26" width="7" height="22"/><rect class="f" x="30" y="30" width="7" height="18"/><rect class="f" x="41" y="18" width="7" height="30"/><path d="M8 24l12-8 10 6 16-14"/></svg>
  <h4>Business &amp;<br>Asset Finance</h4><p style="top:163px">(Business Customers only)</p>
</div>

<!-- row 2 -->
<div class="abs card" style="left:172px;top:1237px">
  <svg class="ico" viewBox="0 0 56 56"><path d="M10 50V22h12v28M22 50V8h24v42M6 50h44M27 15h3M35 15h3M27 23h3M35 23h3M27 31h3M35 31h3M27 39h3M35 39h3M14 30h3M14 38h3"/></svg>
  <h4>Commercial<br>Finance</h4><p style="top:163px">(From $1 million to $50 million)</p>
</div>
<div class="abs card" style="left:390px;top:1237px">
  <svg class="ico" viewBox="0 0 56 56"><path d="M28 5 46 12v14c0 12-8 20-18 25C18 46 10 38 10 26V12z"/><circle cx="28" cy="28" r="10"/><path d="m23 28 4 4 6-7"/></svg>
  <h4>Insurance Rates</h4><p style="top:145px">Lorem ipsum dolor sit am econsectetur adiiscn</p>
</div>
<div class="abs card" style="left:607px;top:1237px">
  <svg class="ico" viewBox="0 0 56 56"><rect class="f" x="8" y="8" width="18" height="14" rx="2"/><path d="M17 22v26M17 32h6M17 40h6M26 14h10v14"/><rect x="30" y="28" width="16" height="20" rx="3"/><rect class="f" x="35" y="34" width="6" height="8"/></svg>
  <h4>Vehicle Leasing</h4><p style="top:145px">Lorem ipsum dolor sit am (comming Soon)</p>
</div>
<div class="abs card" style="left:825px;top:1237px">
  <svg class="ico" viewBox="0 0 56 56"><path d="M28 5 46 12v14c0 12-8 20-18 25C18 46 10 38 10 26V12z"/><path class="f" d="M17 34v-7l4-7h14l4 7v7z"/><circle cx="21" cy="30" r="1.5" fill="#fff" stroke="none"/><circle cx="35" cy="30" r="1.5" fill="#fff" stroke="none"/></svg>
  <h4>Home, Contents &amp;<br>Car Insurance</h4><p style="top:163px">(comming Soon)</p>
</div>

<!-- row 3 -->
<div class="abs card" style="left:172px;top:1467px">
  <svg class="ico" viewBox="0 0 56 56"><path d="M28 30V10"/><path class="f" d="M28 18c-8 0-12-5-12-10 7 0 12 4 12 10zM28 16c0-7 5-11 12-11 0 6-5 11-12 11z"/><path class="f" d="M6 40l10-8c4-2 8-2 12 0h8a3 3 0 0 1 0 6h-8h10l10-6a3 3 0 0 1 3 5L38 48H14l-4 4z"/></svg>
  <h4>Farming &amp; Rural<br>Insurance</h4><p style="top:163px">(comming Soon)</p>
</div>
<div class="abs card" style="left:390px;top:1467px">
  <svg class="ico" viewBox="0 0 56 56"><path d="M22 40c0-6-6-9-6-16a12 12 0 0 1 24 0c0 7-6 10-6 16zM22 45h12M24 50h8M28 3v4M10 10l3 3M46 10l-3 3M4 24h4M48 24h4"/></svg>
  <h4>Power &amp; Gas</h4><p style="top:140px">(comming Soon)</p>
</div>
<div class="abs card" style="left:607px;top:1467px">
  <svg class="ico" viewBox="0 0 56 56"><circle cx="28" cy="28" r="22"/><ellipse cx="28" cy="28" rx="10" ry="22"/><path d="M6 28h44M9 17h38M9 39h38M28 6v44"/></svg>
  <h4>Internet &amp; Fibre</h4><p style="top:144px">(comming Soon)</p>
</div>
<div class="abs card" style="left:825px;top:1467px">
  <svg class="ico" viewBox="0 0 56 56"><rect x="15" y="4" width="26" height="48" rx="4"/><path d="M15 42h26M25 47h6"/></svg>
  <h4>Phone &amp; Mobile</h4><p style="top:144px">(comming Soon)</p>
</div>

<!-- about -->
<section class="abs about">
  <div class="blob-back"></div>
  <div class="blob" role="img" aria-label="Photo of a couple relaxing on a sofa looking at a laptop"></div>
  <h2>ABOUT US</h2>
  <p class="lead">Our goal is to get major banks, insurance companies, utility companies and other consumer service suppliers fighting for the consumer's business.</p>
  <p class="body">With Lendquay, you can submit a form with a few basic details, and get a range of representative offers back in under 90 seconds. These appear on your personal dashboard, and you can then choose, follow up any representative offers displayed completely at your discretion</p>
  <div class="btn-ghost">READ MORE</div>
</section>

<!-- why -->
<h2 class="abs section-title" style="top:2405px">WHY LENDQUAY?</h2>
<p class="abs why-sub">Our mission is to put the power in the hands of the consumer</p>

<div class="abs why" style="left:164px;top:2530px">
  <div class="ring"></div><div class="dot"></div>
  <svg class="ico" viewBox="0 0 56 56"><path d="M4 30h8v18H4zM12 44l14 3 16-8c3-2 1-6-2-5l-10 4M12 32h8l8 4"/><rect x="24" y="8" width="18" height="26" rx="2"/><rect x="30" y="4" width="18" height="26" rx="2"/><circle cx="39" cy="17" r="5"/></svg>
  <h5>GREAT RATES &amp;<br>INCENTIVES</h5>
  <p>Receive the great rates and incentives hassle-free - Lendquay does the shopping around for you.</p>
</div>
<div class="abs why" style="left:390px;top:2530px">
  <div class="ring"></div><div class="dot"></div>
  <svg class="ico" viewBox="0 0 56 56"><circle cx="28" cy="28" r="22"/><circle cx="28" cy="28" r="16"/><path d="M28 16v12l8 6"/></svg>
  <h5>ANY TIME,<br>ANY WHERE</h5>
  <p>Get notifications and review representative offers wherever you are with your personal, mobile-friendly Lendquay dashboard.</p>
</div>
<div class="abs why" style="left:616px;top:2530px">
  <div class="ring"></div><div class="dot"></div>
  <svg class="ico" viewBox="0 0 56 56"><circle cx="22" cy="32" r="9"/><path d="M8 52c0-8 6-13 14-13s14 5 14 13"/><rect x="32" y="16" width="16" height="13" rx="2"/><path d="M35 16v-4a5 5 0 0 1 10 0v4"/></svg>
  <h5>PRIVACY IS<br>IMPORTANT</h5>
  <p>Your private information is disclosed only when you follow up on representative offers from a service provider.</p>
</div>
<div class="abs why" style="left:842px;top:2530px">
  <div class="ring"></div><div class="dot"></div>
  <svg class="ico" viewBox="0 0 56 56"><path d="M30 6h18v18L24 48 6 30z"/><circle cx="40" cy="14" r="3"/><path d="M26 22c-3-2-7 1-4 4s-1 7-4 4M21 20l-2-2M29 31l-2-2"/></svg>
  <h5>NO FEES, NO<br>OBLIGATIONS</h5>
  <p>The Lendquay service is free and you are under no obligation until you select the representative offer that best suits your needs.</p>
</div>

<!-- blog -->
<div class="abs blog-bg"></div>
<h2 class="abs section-title" style="top:2910px">LATEST BLOG</h2>
<div class="abs blog-feature" role="img" aria-label="Photo of a smiling couple looking at a laptop together"></div>
<article class="abs blog-feature-card">
  <div class="date"><svg width="14" height="14" viewBox="0 0 14 14" fill="none" stroke="currentColor" stroke-width="1.5"><rect x="1" y="2.5" width="12" height="10.5" rx="1"/><path d="M1 6h12M4 1v3M10 1v3"/></svg>Oct 31 2020</div>
  <h4>Lorem ipsum dolor sit amet, consec</h4>
  <p>Lorem ipsum dolor sit amet, consectetur adipiscing elit, sed do eiusmod tempor incididunt ut labore et dolore magna aliqua. Ut enim ad minim veniam</p>
</article>

<article class="abs post" style="top:2990px">
  <div class="thumb" role="img" aria-label="Photo of a woman reading documents at home" style="background:linear-gradient(135deg,#7c8796,#3e4452)"></div>
  <div class="txt"><div class="date"><svg width="11" height="11" viewBox="0 0 14 14" fill="none" stroke="currentColor" stroke-width="1.6"><rect x="1" y="2.5" width="12" height="10.5" rx="1"/><path d="M1 6h12M4 1v3M10 1v3"/></svg>Oct 31 2020</div>
  <h6>Finibus Bonorum elorum</h6><p>Sed ut perspiciatis undoree omnis iste natus error sit voluptatem ac</p></div>
</article>
<article class="abs post" style="top:3130px">
  <div class="thumb" role="img" aria-label="Photo of two people embracing outdoors" style="background:linear-gradient(135deg,#5d7267,#8a7a66)"></div>
  <div class="txt"><div class="date"><svg width="11" height="11" viewBox="0 0 14 14" fill="none" stroke="currentColor" stroke-width="1.6"><rect x="1" y="2.5" width="12" height="10.5" rx="1"/><path d="M1 6h12M4 1v3M10 1v3"/></svg>Oct 31 2020</div>
  <h6>Finibus Bonorum elorum</h6><p>Sed ut perspiciatis undoree omnis iste natus error sit voluptatem acc</p></div>
</article>
<article class="abs post" style="top:3272px">
  <div class="thumb" role="img" aria-label="Photo of a businessman shaking hands with a client" style="background:linear-gradient(135deg,#dfe3e7,#4b5a70)"></div>
  <div class="txt"><div class="date"><svg width="11" height="11" viewBox="0 0 14 14" fill="none" stroke="currentColor" stroke-width="1.6"><rect x="1" y="2.5" width="12" height="10.5" rx="1"/><path d="M1 6h12M4 1v3M10 1v3"/></svg>Oct 31 2020</div>
  <h6>Finibus Bonorum elorum</h6><p>Sed ut perspiciatis undoree omnis iste natus error sit voluptatem accusaloren</p></div>
</article>

<!-- footer -->
<footer class="abs footer">
  <div class="email">Email:</div>
  <div class="btn-primary">SIGN UP</div>
  <div class="rule"></div>
  <span class="fnav" style="left:361px">HOME</span>
  <span class="fnav" style="left:447px">ABOUT US</span>
  <span class="fnav" style="left:561px">MEDIA</span>
  <span class="fnav" style="left:648px">SUPPORT</span>
  <span class="fnav" style="left:754px">CONTACT US</span>
  <p class="copy">Copyright 2020 Lendquay. All Rights Reserved</p>
  <span class="social" style="left:521px"></span>
  <span class="social" style="left:550px"></span>
  <span class="social" style="left:583px"></span>
  <span class="social" style="left:615px"></span>
  <span class="social" style="left:647px"></span>
</footer>

</body>
</html>
```